PowerPoint Listing Presentation for Real Estate Agency

We need a PowerPoint presentation for a new real estate brokerage team.

[[[[[[submit 1-3 sample slides for review - i will provide feedback and you can make changes if you want to - we will not be deciding on a design prior to the deadline]]]]]

******ATTN: DESIGNERS, if your skills are webdesign then just look at this like a portable website or a brochure. it should be easy enough******

NOTE: we have all the data to put into the slides. You just need to come up with the design and layout. we have a sample design that we like and have provided.

This focus will be for the home listing side of the business (a presentation for home sellers to convince them to use our services). The data and slides will present our team and the benefits, in the best light, to use our services over that of other real estate agent applying for the job. This presentation will proved facts and benefits and describe our special and unique offerings that will show a home seller why we can sell their home for more money in less time and with the least amount of hassle. The main color scheme is Dark Blue and White (we want some additional colors included - based on your creativity. otherwise the presentation will too monotone). We would like to see the use of Statistical Graphs (3-D) - data provided. We have photos of our team and a new logo (the logo could have some minor adjustment to clean it up if necessary) - also uploaded. We have about 80-90% of the information that will be put into the slides and will need to work closely to get the design and data integrated into the presentation (should be easier then it sounds). We should be able to add slides and data 'at will' over time via our master slides built into the presentation. We have a pretty good sample presentation that we like and can be used as a guideline (this is from our affiliated business network and we have full rights to all the information), it is uploaded but doesn't contain all the slide because of size limitations.

NOTE: An additional buyers presentation will be needed after we get the sellers presentation completed, which means additional work.

This should be enough to get you started and we are available if you have any questions to help you with the project. there will be around 60-70 total slides. once concept is completed it will be easy to create the slides.

Target Market(s)

home sellers. people who are moving to a new and better home or relocation for job reasons. typically more established in life

Industry/Entity Type

Real Estate

Requirements
Must have
• all the slides must be congruent. in other words, the exact same layout feel should used across the board. we are working on building our trade dress/image. Also, it must have a soft and inviting overall feel, yet show strength of ability.
Nice to have
• nice to have use of real people images when necessary. 3D graphs would be nice. clean modern look and feel, yet sophisticated and professional.
Should not have
• should not have a lot of time consuming transitions. do not include 3D stick figures or distracting moving gifs

```html
<!DOCTYPE html>
<html lang="en">
<head>
<meta charset="UTF-8">
<title>Our VIP Seller Benefits</title>
<link href="https://fonts.googleapis.com/css2?family=Libre+Baskerville:wght@400;700&display=swap" rel="stylesheet">
<style>
  :root {
    --navy: #0d2a5c;
    --navy-deep: #082149;
    --accent-blue: #1c4fa8;
    --sky: #5b8ede;
    --sky-pale: #e4ecf8;
    --gold: #f2b417;
    --ink: #1c2b44;
    --white: #ffffff;
    --serif: "Libre Baskerville", Georgia, serif;
  }
  * { margin: 0; padding: 0; box-sizing: border-box; }
  html, body { width: 1200px; height: 900px; overflow: hidden; background: var(--white); }
  .slide {
    position: relative;
    width: 1200px;
    height: 900px;
    overflow: hidden;
    font-family: var(--serif);
    color: var(--ink);
    background: linear-gradient(160deg, var(--white) 20%, var(--sky-pale) 75%);
  }
  .slide-frame { position: absolute; inset: 0; width: 1200px; height: 900px; }

  .slide-title {
    position: absolute;
    top: 48px;
    left: 600px;
    display: flex;
    align-items: center;
    gap: 18px;
  }
  .title-badge { width: 64px; height: 64px; flex: none; }
  .slide-title h1 {
    font-weight: 400;
    font-size: 38px;
    letter-spacing: -0.5px;
    color: var(--navy);
    white-space: nowrap;
  }
  .slide-title h1 .title-accent { color: var(--accent-blue); }

  .benefit-list { list-style: none; position: absolute; left: 60px; top: 318px; width: 920px; }
  .benefit {
    position: relative;
    padding-left: 82px;
    font-size: 27px;
    line-height: 58px;
    color: var(--ink);
  }
  .benefit + .benefit { margin-top: 55px; }
  .benefit-tick { position: absolute; left: 0; top: 6px; width: 52px; height: 52px; }
  .benefit .emphasis { font-weight: 700; color: var(--accent-blue); font-size: 22px; }
  .benefit .shout { font-weight: 700; color: var(--accent-blue); font-size: 22px; text-transform: uppercase; }

  .brand {
    position: absolute;
    left: 985px;
    top: 770px;
    display: flex;
    align-items: center;
    gap: 12px;
    font-family: var(--serif);
    font-size: 22px;
    font-weight: 400;
    color: var(--white);
    white-space: nowrap;
  }
  .brand-square { width: 18px; height: 18px; background: var(--white); flex: none; }
</style>
</head>
<body>
<main class="slide">
  <svg class="slide-frame" viewBox="0 0 1200 900" aria-hidden="false">
    <defs>
      <linearGradient id="houseTone" x1="0" y1="0" x2="0" y2="1">
        <stop offset="0" stop-color="#d3e0f2" stop-opacity="0.55"/>
        <stop offset="1" stop-color="#d3e0f2" stop-opacity="0.15"/>
      </linearGradient>
    </defs>
    <rect class="house-backdrop" x="20" y="210" width="1060" height="520" rx="10" fill="url(#houseTone)" role="img" aria-label="Faint illustration of a row of houses"/>

    <!-- top-left corner band -->
    <path d="M0 0 H440 C300 70 130 180 0 330 Z" fill="var(--sky)"/>
    <path d="M0 0 H405 C275 65 115 170 0 300 Z" fill="var(--navy)"/>

    <!-- bottom-right corner band -->
    <path d="M1200 270 C1100 590 880 820 560 900 H1200 Z" fill="var(--gold)"/>
    <path d="M1200 292 C1108 600 900 830 600 900 H1200 Z" fill="var(--sky)"/>
    <path d="M1200 315 C1118 610 920 840 648 900 H1200 Z" fill="var(--navy-deep)"/>
  </svg>

  <header class="slide-title">
    <svg class="title-badge" viewBox="0 0 64 64" aria-hidden="true">
      <circle cx="32" cy="32" r="30" fill="var(--navy)" stroke="var(--sky)" stroke-width="3"/>
    </svg>
    <h1>Our VIP Seller <span class="title-accent">Benefits</span></h1>
  </header>

  <ul class="benefit-list">
    <li class="benefit">
      <svg class="benefit-tick" viewBox="0 0 52 52" aria-hidden="true">
        <circle cx="24" cy="28" r="20" fill="var(--gold)"/>
        <circle cx="24" cy="28" r="15" fill="var(--white)"/>
        <path d="M14 27 L22 36 L44 8" fill="none" stroke="var(--navy)" stroke-width="7" stroke-linecap="round" stroke-linejoin="round"/>
      </svg>
      Your Home Sold at a Price Acceptable to You<br>
      <span class="emphasis">(Guaranteed in Writing)</span> or We’ll Buy it for Cash!
    </li>
    <li class="benefit">
      <svg class="benefit-tick" viewBox="0 0 52 52" aria-hidden="true">
        <circle cx="24" cy="28" r="20" fill="var(--gold)"/>
        <circle cx="24" cy="28" r="15" fill="var(--white)"/>
        <path d="M14 27 L22 36 L44 8" fill="none" stroke="var(--navy)" stroke-width="7" stroke-linecap="round" stroke-linejoin="round"/>
      </svg>
      Buy Any One of Our Listings and if YOU Are Not<br>
      Satisfied in 24 Months <span class="shout">We’ll Buy It Back!</span>
    </li>
  </ul>

  <div class="brand"><span class="brand-square"></span>Harrow &amp; Vale</div>
</main>
</body>
</html>
```